Brochure Design Project - Glass Cabinets

We are a small but rapidly expanding company providing glass display furniture to retailers and other organisations to display their product. We specialise in all-glass, frameless display cabinets and showcases. Our products include glass cabinets, wall units, shelving units, etc. Our main market was initially householders, then retailers, but has increasingly become corporates who want to display their corporate prizes/trophies, and are also fit-out companies who have discovered our products and are interested in them. We want to make the most of this development, and we want this brochure to help us.
We have identified shop fit-out companies and fit-out designers as a target market for the coming year, so we need some literature that will introduce our company to these businesses, and encourage them to use our products in their designs.
This brochure will not be a product catalogue (we already have that), but a corporate profile that introduces our company and its services. We need to communicate the message that we are a serious provider of good quality glass display furniture, and that we stand for innovation, value, and good design.
We will be giving these brochures out when we make marketing approaches to the shop fit-out companies.
We envisage that the brochure will be a one A4 page brochure, with the back side used for examples of our work. We are open to suggestions about this, however. For example, it could conceivably be DLE format.
We expect some of the copy will be in text boxes. We will upload further details of the examples on page 2 in the next few days.
It needs to be full colour.
It will be offset printed.
The output needs to be PC compatible, preferably produced in Indesign so it is compatible with our software.
Please see our website and other uploaded files for examples of our current imagery. The corporate brochure needn't follow this slavishly, but should be cognizant of it.

Reason: The deadline has been extended because there is some further information I will put up, regarding page two. Also, I will spend some time providing feedback.

Thank you to all who have submitted designs for my project. They are all very much appreciated. I have responded to most of you, but some general comments that come to mind are that the brochure needs to 1) appeal to the emotions more i.e. be more evocative of sophistication. This means not necessarily using just the images I have uploaded, but maybe suggest design elements that are more creative than 'blocky', and 2) be designed to sell the company rather than its products. This is partly my fault, I think, although it is a learning experience for me also. In general I think there is too much information to include, especially copy but also images, forcing designers to make the designs quite boring in order to accommodate it. I intend to cut the information significantly and will repost. Having said that, I am trying to see through the overload of information and look for designs that include elements that are creative and sophisticated. Sometimes less is more. Apologies if I am confusing you, but the main thing is to make the brochure appeal to the emotions i.e. 'this company is sophisticated and and be depended upon', and less to the products themselves. I welcome any questions you may have.

Thanks to all the designers who have submitted designs. There are some great ideas coming through now, and on the basis of these ideas I have been able to determine what the brochure needs to look like much more precisely. Some of the designs have been too crowded, because there has been too much information to include. I have therefore decided that the brochure needs to be a 4 page A4 brochure (A3 folded in half). I have altered the copy in the Word document to reflect this. The middle spread is now dedicated to jobs previously done, and includes logos of other high profile customers. The front page can now be dedicated to providing very basic, introductory information and an eye-catching graphic, while the back page has further detail about the company and contact details. To reflect the fact that this will involve some redesign work, I have increased the budget. I have also extended the deadline by a week. I thank you for your patience, but sometimes a design project is iterative. Please see the newly uploaded files.

Reason: Thanks to all the designers who have submitted designs. There are some great ideas coming through now, and on the basis of these ideas I have been able to determine what the brochure needs to look like much more precisely. Some of the designs have been too crowded, because there has been too much information to include. I have therefore decided that the brochure needs to be a 4 page A4 brochure (A3 folded in half). I have altered the copy in the Word document to reflect this. The middle spread is now dedicated to jobs previously done, and includes logos of other high profile customers. The front page can now be dedicated to providing very basic, introductory information and an eye-catching graphic, while the back page has further detail about the company and contact details. To reflect the fact that this will involve some redesign work, I have increased the budget. I have also extended the deadline by a week. I thank you for your patience, but sometimes a design project is iterative. Please see the newly uploaded files.

Target Market(s)

Shop Fit-out companies, Fit-out designers, Retailers

Industry/Entity Type

Marketing

Requirements
Must have
• Existing logo
Full colour, with overprint

```html
<!DOCTYPE html>
<html lang="en">
<head>
<meta charset="utf-8">
<title>Clearline Displays – Brochure Cover</title>
<link rel="stylesheet" href="https://fonts.googleapis.com/css2?family=Hind:wght@600&family=Open+Sans:wght@400;700&display=swap">
<style>
  :root {
    --backdrop: #d4d0d4;
    --paper: #ffffff;
    --plum: #4b3150;
    --leaf: #a4bc55;
    --leaf-pale: #c9d89a;
    --glass-light: #eef4f3;
    --glass-mid: #cddbd9;
    --plush-deep: #9c4e26;
    --plush-mid: #c47844;
    --plush-cream: #efe4da;
    --white: #ffffff;
  }
  * { box-sizing: border-box; margin: 0; padding: 0; }
  html, body { width: 1200px; height: 900px; overflow: hidden; }
  body { background: var(--backdrop); font-family: "Open Sans", Arial, sans-serif; color: var(--plum); }

  .spread { position: absolute; left: 76px; top: 86px; width: 1052px; height: 744px; background: var(--paper); }

  .headline {
    position: absolute; font-family: "Hind", "Trebuchet MS", sans-serif; font-weight: 600;
    font-size: 30px; line-height: 36px; text-align: center; color: var(--plum); white-space: nowrap;
  }
  .headline--intro { left: 6px; width: 300px; top: 100px; }
  .headline--cover { left: 766px; width: 258px; top: 100px; }

  .visual { position: absolute; }
  .visual--glass-cubes { left: 64px; top: 270px; width: 194px; height: 196px;
    background: linear-gradient(165deg, var(--glass-light) 0%, var(--glass-mid) 60%, #dfe8e6 100%); }
  .visual--plush-toy { left: 767px; top: 247px; width: 258px; height: 252px;
    background: radial-gradient(ellipse 62% 62% at 52% 55%, var(--plush-deep) 0%, var(--plush-mid) 45%, #dcae8c 75%, var(--plush-cream) 100%); }

  .cta { position: absolute; left: 52px; top: 597px; width: 180px; height: 54px; }
  .cta__label { position: absolute; left: 32px; top: 0; width: 148px; height: 54px;
    display: flex; align-items: center; justify-content: center; text-align: center;
    color: var(--white); font-weight: 700; font-size: 11.5px; line-height: 15px; }

  .value-band { position: absolute; left: 308px; top: 0; width: 64px; height: 744px; background: var(--leaf); }
  .value-band__words { position: absolute; left: 32px; top: 372px; width: 542px;
    transform: translate(-50%, -50%) rotate(-90deg);
    display: flex; justify-content: space-between;
    color: var(--white); font-weight: 700; font-size: 24px; letter-spacing: 2px; }

  .contact { position: absolute; left: 415px; top: 100px; width: 280px; font-size: 13px; line-height: 18px; }
  .contact__invite { margin-bottom: 26px; }
  .contact__details { text-align: center; }

  .brand { position: absolute; display: flex; align-items: center; gap: 8px;
    font-weight: 700; font-size: 17px; color: var(--leaf); letter-spacing: 0.3px; }
  .brand__mark { width: 28px; height: 28px; background: var(--leaf-pale); }
  .brand--back { left: 444px; top: 596px; }
  .brand--cover { left: 786px; top: 596px; }

  .partner-badge { position: absolute; left: 505px; top: 651px; width: 107px; height: 53px; background: var(--leaf); }
</style>
</head>
<body>
  <main class="spread">
    <h2 class="headline headline--intro">Presenting our<br>good quality<br>all-glass frameless<br>displays.</h2>
    <div class="visual visual--glass-cubes" role="img" aria-label="Photo: stacked all-glass frameless display cubes holding soft toys"></div>

    <div class="cta">
      <svg width="180" height="54" viewBox="0 0 180 54" aria-hidden="true">
        <polygon points="2,27 40,11 40,43" fill="var(--leaf)"/>
        <rect x="32" y="0" width="148" height="54" rx="27" fill="var(--leaf)"/>
      </svg>
      <p class="cta__label">Why glass?<br>Find out why?</p>
    </div>

    <div class="value-band">
      <div class="value-band__words"><span>UNIQUE</span><span>INNOVATIVE</span><span>CREATIVE</span></div>
    </div>

    <section class="contact">
      <p class="contact__invite">Contact us now to discuss your requirements.</p>
      <p class="contact__details">
        Mara Quinlan (Director)<br>
        Ph. 0275550148<br>
        Fax (09) 5550172<br>
        email: mara@clearlinedisplays.co.nz<br>
        website: www.clearlinedisplays.co.nz
      </p>
    </section>

    <div class="brand brand--back"><span class="brand__mark"></span><span>CLEARLINE DISPLAYS</span></div>
    <div class="partner-badge" role="img" aria-label="Preferred supplier badge"></div>

    <h1 class="headline headline--cover">We have the<br>perfect place to<br>show it off.</h1>
    <div class="visual visual--plush-toy" role="img" aria-label="Photo: soft plush toy sitting upright"></div>
    <div class="brand brand--cover"><span class="brand__mark"></span><span>CLEARLINE DISPLAYS</span></div>
  </main>
</body>
</html>
```